Brenwick Structures Construction Company Seeking Modern Website

We are a small construction company wanting to create a web presence. We don't have much in the way of current content but will get photos as they come in. Attached is a picture of our business card.
The pages we would like on the menu are:
Home
Portfolio
Product Specs
Testimonials
Our Process
Contact
Some designs we like are:
http://www.tovasheds-example.com/
http://www.qrnstructures-example.com/
http://dunholtbarns-example.com/
http://pellingframes-example.com/
Not much requirements other than that so feel free to be creative!
Updates
Target Market(s)
Construction
Commercial and Residential Buildings
Industry/Entity Type
Construction Company
Number of Pages Required
5+ page
Look and feel

```html
<!DOCTYPE html>
<html lang="en">
<head>
<meta charset="utf-8">
<title>Brenwick Structures</title>
<link href="https://fonts.googleapis.com/css2?family=Arimo:wght@400;700&family=Open+Sans:wght@400;600;700&display=swap" rel="stylesheet">
<style>
:root{
  --red:#d8261e;
  --dark:#333333;
  --text:#6b6b6b;
  --footer:#5a5a5a;
  --footer-line:#7a7a7a;
  --white:#ffffff;
  --brand:#1f74c0;
  --card:#f4f4f4;
}
*{margin:0;padding:0;box-sizing:border-box}
html,body{width:900px;height:1200px;overflow:hidden;background:var(--white)}
body{position:relative;font-family:'Arimo',Arial,sans-serif;color:var(--text)}
.abs{position:absolute}
.brand{left:76px;top:56px;font-size:22px;font-weight:700;color:var(--brand);font-family:'Arimo',Arial,sans-serif;white-space:nowrap}
.phone{left:610px;top:33px;font-size:16px;color:var(--dark);display:flex;align-items:center;gap:6px}
.social-top{left:739px;top:31px;display:flex;gap:9px}
.social-top span{width:23px;height:23px;border:1.5px solid #888;border-radius:50%}
.nav{left:346px;top:69px;display:flex;align-items:center;font-size:11.5px;color:var(--dark)}
.nav a{color:var(--dark);text-decoration:none;margin-right:28px;white-space:nowrap}
.nav a.active{background:var(--red);color:var(--white);padding:6px 11px;border-radius:3px;margin-right:22px}
.hero{left:0;top:110px;width:900px;height:508px;background:linear-gradient(180deg,#f6a623 0%,#f8b433 45%,#3b2a10 80%,#000 100%)}
.card{top:504px;width:233px;height:251px;background:linear-gradient(#fff,var(--card));box-shadow:0 2px 3px rgba(0,0,0,.12);text-align:center}
.card .photo{height:141px}
.card h3{font-family:'Open Sans',sans-serif;font-weight:600;color:var(--red);font-size:12px;margin-top:10px}
.card p{font-size:10px;line-height:16.6px;padding:0 10px;margin-top:3px}
.more{color:var(--red);font-size:10px;margin-top:7px;display:inline-block}
.welcome{left:76px;top:800px;width:425px}
h2{font-family:'Open Sans',sans-serif;font-weight:400;font-size:16px;color:var(--dark)}
h2 em{font-style:normal;color:var(--red);font-weight:600}
.welcome p{font-size:10.2px;line-height:16.6px;margin-top:9px}
.news{left:539px;top:798px;width:290px}
.item{display:flex;gap:14px;margin-top:13px}
.item .photo{width:104px;height:59px;flex:none}
.item .date{color:var(--red);font-weight:700;font-size:9.6px}
.item p{font-size:9.8px;line-height:15.2px;margin-top:1px}
.item u{color:var(--red)}
.footer{left:0;top:1013px;width:900px;height:187px;background:var(--footer);color:var(--white)}
.footer h4{position:absolute;top:14px;font-size:12px;font-weight:700;letter-spacing:.3px}
.signup{left:80px;top:45px;display:flex}
.signup .input{width:158px;height:27px;background:var(--white);color:#999;font-size:8px;display:flex;align-items:center;padding-left:8px;gap:6px}
.signup .btn{width:75px;height:27px;background:var(--red);font-size:12px;display:flex;align-items:center;justify-content:center}
.links{left:384px;top:41px;font-size:10px;line-height:18px}
.follow{left:539px;top:40px;font-size:11px}
.follow div{display:flex;align-items:center;gap:9px;height:38px}
.follow i{width:24px;height:24px;border-radius:50%;background:#dfe9f3;border:3px solid #eef2f6;display:block}
.contact{left:699px;top:50px;font-size:10px;line-height:16px}
.contact strong{font-size:13.5px;display:block;margin-bottom:5px}
.rule{left:75px;top:1170px;width:750px;height:1px;background:var(--footer-line)}
.copy{left:0;top:1177px;width:900px;text-align:center;color:var(--white);font-size:9.6px}
</style>
</head>
<body>
<div class="abs brand">Brenwick Structures</div>
<div class="abs phone"><svg width="12" height="14" viewBox="0 0 12 14"><path d="M2 1l3 0 1 3-2 1.5c.8 2 2 3.4 3.6 4.3L9 8l3 1v3c-5 1-11-5-10-11z" fill="#d8261e"/></svg>98 30461572</div>
<div class="abs social-top"><span></span><span></span><span></span></div>
<nav class="abs nav"><a class="active">Home</a><a>Portfolio</a><a>Product Specs</a><a>Testimonials</a><a>Our Process</a><a style="margin-right:0">Contact</a></nav>

<div class="abs hero" role="img" aria-label="Silhouettes of construction workers and cranes against an orange sunset"></div>

<div class="abs card" style="left:75px">
  <div class="photo" role="img" aria-label="Worker in hard hat cutting on a building site" style="background:linear-gradient(#7ea6d0,#c9c5b8)"></div>
  <h3>ABOUT OUR WORK</h3>
  <p>Lorem ipsum dolor sit amet, consectetur adipi-scing elit, sed do eiusmod tempor incididunt ut labore et dolore magna aliqua.</p>
  <span class="more">Read More »</span>
</div>
<div class="abs card" style="left:333px">
  <div class="photo" role="img" aria-label="Two-storey stone and siding family house" style="background:linear-gradient(#9dbbe0,#8a7a66 60%,#5b7a3a)"></div>
  <h3>RESIDENTIAL</h3>
  <p>Lorem ipsum dolor sit amet, consectetur adipi-scing elit, sed do eiusmod tempor incididunt ut labore et dolore magna aliqua.</p>
  <span class="more">Read More »</span>
</div>
<div class="abs card" style="left:592px">
  <div class="photo" role="img" aria-label="Modern building with timber and white facade at dusk" style="background:linear-gradient(#6b8fc0,#b89070 55%,#4c6a35)"></div>
  <h3>COMMERCIAL</h3>
  <p>Lorem ipsum dolor sit amet, consectetur adipi-scing elit, sed do eiusmod tempor incididunt ut labore et dolore magna aliqua.</p>
  <span class="more">Read More »</span>
</div>

<section class="abs welcome">
  <h2>Welcome To <em>Brenwick Structures</em></h2>
  <p>Lorem ipsum dolor sit amet, consectetur adipiscing elit, sed do eiusmod tempor incididunt ut labore et dolore magna aliqua. Ut enim ad minim veniam, quis nostrud exercitation ullamco laboris nisi ut aliquip ex ea commodo consequat. Duis aute irure dolor in reprehenderit in voluptate velit esse cillum dolore eu fugiat nulla pariatur Sed ut perspiciatis unde omnis iste natus error sit voluptatem accusantium doloremque laudantium. sed quia non numquam eius modi tempora incidunt ut labore et dolore magnam.</p>
  <span class="more" style="margin-top:8px">Read More »</span>
</section>

<section class="abs news">
  <h2>Latest <em>News</em></h2>
  <div class="item">
    <div class="photo" role="img" aria-label="Engineers in hard hats reviewing plans" style="background:linear-gradient(135deg,#e8c020,#9aa8b8 50%,#e0e4ea)"></div>
    <div><div class="date">Nov 11,2015</div><p>Ut enim ad minim veniam, quis nostrud exercitation quia non nisi ut aliquip commodo... <u>Read More</u></p></div>
  </div>
  <div class="item" style="margin-top:17px">
    <div class="photo" role="img" aria-label="Workers silhouetted at sunset on a site" style="background:linear-gradient(#f6a623,#2a1c08)"></div>
    <div><div class="date">July 25,2015</div><p>Ut enim ad minim veniam, quis nostrud exercitation quia non nisi ut aliquip commodo... <u>Read More</u></p></div>
  </div>
</section>

<footer class="abs footer">
  <h4 style="left:80px">SUBSCRIBE TO OUR NEWSLETTER</h4>
  <h4 style="left:381px">QUICK LINKS</h4>
  <h4 style="left:537px">FOLLOW US</h4>
  <h4 style="left:699px">CONTACT</h4>
  <div class="abs signup">
    <div class="input"><svg width="20" height="13" viewBox="0 0 20 13"><rect x=".5" y=".5" width="19" height="12" fill="none" stroke="#bbb"/><path d="M.5.5l9.5 7 9.5-7" fill="none" stroke="#bbb"/></svg>Type Your email address</div>
    <div class="btn">Subscribe</div>
  </div>
  <div class="abs" style="left:80px;top:90px;font-size:11px">Our Newsletter Signup</div>
  <div class="abs" style="left:81px;top:109px;width:240px;font-size:9.6px;line-height:15.5px;color:#e6e6e6">Lorem ipsum dolor sit amet, consectetur adipiscing elit, sed do eiusmod tempor incididunt.</div>
  <div class="abs links">Home<br>About Us<br>Services<br>Portfolio<br>Contact Us</div>
  <div class="abs follow">
    <div><i></i>Chirpline</div>
    <div><i></i>Friendspace</div>
    <div><i></i>Workmesh</div>
  </div>
  <div class="abs contact"><strong><svg width="10" height="11" viewBox="0 0 12 14"><path d="M2 1l3 0 1 3-2 1.5c.8 2 2 3.4 3.6 4.3L9 8l3 1v3c-5 1-11-5-10-11z" fill="#fff"/></svg> 9830461572</strong>48 Corvale Street,<br>Redmont Bay Wa 6102</div>
</footer>
<div class="abs rule"></div>
<div class="abs copy">Copyright © 2013.All right reserved</div>
</body>
</html>
```